Innovative tech company looking for a new look for business card

We need a business card revamp- our current design is amazingly dated and in need of a new vision. The Delta is logo that is used, but other than that and the company name - we are open to everything- red is the color of choice typically due to delta. QV is a National credit reporting agency servicing lending institutions for more than 24 years.

***We want a minimal, clean design, we want to move away from the harsh- red, black and white feel. The files uploaded are to show what we are currently using and exactly what we want to move AWAY from.

Thanks you to all!

We are looking for a "lighter" feel more "plumwick-esque." We want to move away from the harsh black , white, and red. The files I uploaded were more to show what we currently have and really want to move away from. I am going to edit the brief to be sure this is expressed.

Reason: Still looking for options....

Reason: Still looking for more designs -

```html
<!DOCTYPE html>
<html lang="en">
<head>
<meta charset="utf-8">
<title>Quorvane Credit, Inc. — Business Card</title>
<link rel="stylesheet" href="https://fonts.googleapis.com/css2?family=Lato:wght@400;700&display=swap">
<style>
  :root {
    --bg: #e6e7ea;
    --card: #ffffff;
    --brand-blue: #2b4d93;
    --band-blue: #2f5ea8;
    --band-deep: #23478a;
    --logo-grey: #8a8c90;
    --rule-grey: #b9bbbf;
    --ink: #1e2430;
    --white: #ffffff;
  }
  * { box-sizing: border-box; margin: 0; padding: 0; }
  html, body { width: 1200px; height: 680px; overflow: hidden; }
  body {
    background: var(--bg);
    font-family: "Lato", sans-serif;
    color: var(--ink);
    position: relative;
  }
  .card {
    position: absolute;
    top: 192px;
    width: 520px;
    height: 297px;
    background: var(--card);
    border-radius: 6px;
    box-shadow: 0 6px 22px rgba(30, 36, 48, 0.16);
    overflow: hidden;
  }
  .card--front { left: 50px; }
  .card--back { left: 630px; }

  .brand {
    display: flex;
    align-items: center;
    gap: 12px;
  }
  .brand__dot {
    width: 22px; height: 22px;
    border-radius: 50%;
    background: var(--brand-blue);
    flex: none;
  }
  .brand__name {
    font-size: 25px;
    font-weight: 400;
    color: var(--logo-grey);
    letter-spacing: 0.5px;
    white-space: nowrap;
  }
  .brand-rule {
    height: 1px;
    background: var(--rule-grey);
  }

  /* Front */
  .card--front .brand { position: absolute; left: 30px; top: 30px; }
  .card--front .brand-rule { position: absolute; left: 30px; right: 30px; top: 76px; }

  .person { position: absolute; left: 30px; top: 104px; }
  .person__name { font-size: 21px; color: var(--brand-blue); }
  .person__role { font-size: 13px; color: var(--ink); margin-left: 4px; }

  .address {
    position: absolute; left: 30px; top: 150px;
    display: flex; gap: 10px;
    font-size: 14px; line-height: 1.3;
  }
  .contacts {
    position: absolute; left: 300px; top: 100px;
    list-style: none;
    font-size: 13px; line-height: 1.45;
  }
  .contacts li, .address { align-items: flex-start; }
  .contacts li { display: flex; align-items: center; gap: 7px; }
  .icon { width: 13px; height: 13px; fill: var(--brand-blue); flex: none; }
  .address .icon { margin-top: 2px; }

  .band {
    position: absolute; left: 0; right: 0; bottom: 0;
    height: 46px;
    background: linear-gradient(90deg, var(--band-deep), var(--band-blue));
    border-top-left-radius: 26px;
    display: flex; align-items: center; justify-content: center;
    color: var(--white);
    font-size: 15px; font-weight: 700;
    letter-spacing: 2px;
  }

  /* Back */
  .card--back .logo-block {
    position: absolute; left: 50%; top: 92px;
    transform: translateX(-50%);
    width: 400px;
  }
  .card--back .brand { justify-content: center; }
  .card--back .brand__name { font-size: 28px; }
  .card--back .brand-rule { margin-top: 12px; }
  .back-url {
    position: absolute; left: 0; right: 0; top: 196px;
    text-align: center;
    font-size: 15px; letter-spacing: 0.5px;
    color: var(--ink);
  }
</style>
</head>
<body>

<section class="card card--front" aria-label="Business card front">
  <div class="brand">
    <span class="brand__dot"></span>
    <span class="brand__name">Quorvane Credit, Inc.</span>
  </div>
  <div class="brand-rule"></div>

  <p class="person">
    <span class="person__name">Maren Holt</span>
    <span class="person__role">Business Analyst</span>
  </p>

  <ul class="contacts">
    <li>
      <svg class="icon" viewBox="0 0 16 16" aria-hidden="true"><path d="M3.6 1.2l2.3 2.6-1.3 1.8c.9 2 2.4 3.5 4.4 4.4l1.8-1.3 2.6 2.3-1.5 2.3C6.3 13.2 2.8 9.7 1.3 2.7z"/></svg>
      Direct 555 014 2080
    </li>
    <li>
      <svg class="icon" viewBox="0 0 16 16" aria-hidden="true"><path d="M4 1h8v4H4zM1 6h14v6h-3v3H4v-3H1zm4 4v3h6v-3z"/></svg>
      Direct 555 014 2180
    </li>
    <li>
      <svg class="icon" viewBox="0 0 16 16" aria-hidden="true"><path d="M1 3h14v10H1zm1.5 1.5L8 9l5.5-4.5z"/></svg>
      hello@QuorvaneCredit.com
    </li>
  </ul>

  <div class="address">
    <svg class="icon" viewBox="0 0 16 16" aria-hidden="true"><path d="M8 1.5l7 6h-2v7H9.5v-4h-3v4H3v-7H1z"/></svg>
    <p>2710 N. Alder Crest Road<br>Fernbrook, Ohio<br>USA 43920-1157</p>
  </div>

  <div class="band">www.QuorvaneCredit.com</div>
</section>

<section class="card card--back" aria-label="Business card back">
  <div class="logo-block">
    <div class="brand">
      <span class="brand__dot"></span>
      <span class="brand__name">Quorvane Credit, Inc.</span>
    </div>
    <div class="brand-rule"></div>
  </div>
  <p class="back-url">www.QuorvaneCredit.com</p>
</section>

</body>
</html>
```